Product Description Graphic

We are designing a new product and need a better graphic to describe it.

We are not worried about names of the modules yet but want to be descriptive of capabilities. Right now "Present & CMA" should really be "Presentations & CMA".

I overall like the shape of the triangle and the arrow for Contacts but this is a very unsophisticated graphic done by a non-designer. Also need to better show that each block of capabilites will also have paywall capabilities.

Target Market(s)

Real Estate Brokerage Firms and Real Estate Agents

Industry/Entity Type

Real Estate

Colors

Designer to choose colors to be used in the design.

Requirements
Must have
• Sophisticated design. Paywall description embedded.

```html
<!DOCTYPE html>
<html lang="en">
<head>
<meta charset="utf-8">
<title>Product Capabilities Pyramid</title>
<link rel="stylesheet" href="https://fonts.googleapis.com/css2?family=PT+Sans:wght@400;700&display=swap">
<style>
  :root {
    --bg-light: #ffffff;
    --bg-mid: #f1f1f1;
    --bg-dark: #cfcfcf;
    --email-base: #1e6a95;
    --email-pay: #4a88ac;
    --present-base: #b7843a;
    --present-pay: #c59c60;
    --contacts-base: #50617c;
    --contacts-pay: #273a5c;
    --web-base: #d7847b;
    --web-pay: #cf6961;
    --mobile-base: #688886;
    --mobile-pay: #40696a;
    --label: #ffffff;
    --legend-swatch: #9a9b9b;
    --legend-text: #3d3d3d;
  }
  html, body {
    margin: 0;
    padding: 0;
    width: 1200px;
    height: 1000px;
    overflow: hidden;
  }
  body {
    background: radial-gradient(ellipse 95% 110% at 25% 20%, var(--bg-light) 0%, var(--bg-mid) 50%, var(--bg-dark) 100%);
    font-family: "PT Sans", sans-serif;
  }
  .pyramid {
    position: absolute;
    left: 0;
    top: 0;
    width: 1200px;
    height: 1000px;
  }
  .module-label {
    font-family: "PT Sans", sans-serif;
    font-weight: 700;
    font-size: 20px;
    fill: var(--label);
  }
  .icon {
    fill: none;
    stroke: var(--label);
    stroke-width: 1.6;
    stroke-linecap: round;
    stroke-linejoin: round;
  }
  .icon-fill { fill: var(--label); stroke: none; }
  .legend {
    position: absolute;
    left: 944px;
    top: 914px;
    width: 167px;
    height: 41px;
    display: flex;
    background: #ffffff;
  }
  .legend-swatch {
    width: 33px;
    height: 100%;
    background: var(--legend-swatch);
  }
  .legend-text {
    margin: 0;
    padding: 5px 0 0 9px;
    font-size: 11.5px;
    line-height: 14.5px;
    color: var(--legend-text);
  }
</style>
</head>
<body>
<svg class="pyramid" viewBox="0 0 1200 1000" xmlns="http://www.w3.org/2000/svg" aria-label="Product capability modules arranged as a pyramid">
  <defs>
    <filter id="block-shadow" x="-10%" y="-10%" width="120%" height="130%">
      <feDropShadow dx="0" dy="6" stdDeviation="6" flood-color="#000" flood-opacity="0.22"/>
    </filter>
  </defs>

  <!-- Email, nurture, print & social -->
  <g class="module module-email" filter="url(#block-shadow)">
    <path fill="var(--email-base)" d="M186,698 L583,86 Q601,58 620,84 L640,114 L254,698 Z"/>
    <path fill="var(--email-pay)" d="M640,114 L708,220 L398,698 L254,698 Z"/>
  </g>

  <!-- Presentations & CMA -->
  <g class="module module-present" filter="url(#block-shadow)">
    <path fill="var(--present-pay)" d="M613,409 L680,307 L943,698 L800,698 Z"/>
    <path fill="var(--present-base)" d="M680,307 L722,242 L1015,698 L943,698 Z"/>
  </g>

  <!-- Contacts arrow -->
  <g class="module module-contacts" filter="url(#block-shadow)">
    <path fill="var(--contacts-base)" d="M599,430 L774,698 L665,698 L665,814 L535,814 L535,698 L425,698 Z"/>
    <rect fill="var(--contacts-pay)" x="535" y="814" width="130" height="56"/>
  </g>

  <!-- Websites & leads -->
  <g class="module module-web" filter="url(#block-shadow)">
    <path fill="var(--web-base)" d="M170,721 L512,721 L512,814 L109,814 Z"/>
    <path fill="var(--web-pay)" d="M109,814 L512,814 L512,870 L106,870 Q80,868 92,846 Z"/>
  </g>

  <!-- Mobile -->
  <g class="module module-mobile" filter="url(#block-shadow)">
    <path fill="var(--mobile-base)" d="M688,721 L1030,721 L1091,814 L688,814 Z"/>
    <path fill="var(--mobile-pay)" d="M688,814 L1091,814 L1108,840 Q1120,868 1094,870 L688,870 Z"/>
  </g>

  <!-- Email icon -->
  <g class="icon" transform="translate(480,384)">
    <circle cx="0" cy="1" r="10"/>
    <path class="icon-fill" d="M0,6 L-5,1 A3,3 0 0 1 0,-3 A3,3 0 0 1 5,1 Z"/>
    <rect x="-28" y="-23" width="17" height="12" rx="2"/>
    <path d="M-28,-23 L-19.5,-16 L-11,-23"/>
    <rect x="11" y="-23" width="17" height="12" rx="2"/>
    <path class="icon-fill" d="M17,-20 L23,-17 L17,-14 Z"/>
    <rect x="-28" y="13" width="17" height="12" rx="2"/>
    <circle cx="-19.5" cy="19" r="3"/>
    <rect x="11" y="13" width="17" height="12" rx="2"/>
    <path d="M15,22 V19 M19,22 V17 M23,22 V15"/>
    <path d="M-11,-11 L-7,-6 M11,-11 L7,-6 M-11,13 L-7,8 M11,13 L7,8"/>
  </g>
  <text class="module-label" x="463" y="446" text-anchor="middle">EMAIL, NURTURE</text>
  <text class="module-label" x="463" y="469" text-anchor="middle">PRINT &amp; SOCIAL</text>

  <!-- Presentation board icon -->
  <g class="icon" transform="translate(800,470)">
    <rect x="-22" y="-18" width="44" height="32" rx="2"/>
    <path d="M-12,8 V0 M-4,8 V-8 M4,8 V-4 M12,8 V-11"/>
    <path d="M0,14 V22 M-8,28 L0,22 L8,28"/>
  </g>
  <text class="module-label" x="804" y="537" text-anchor="middle">PRESENTATIONS</text>
  <text class="module-label" x="804" y="560" text-anchor="middle">&amp; CMA</text>

  <!-- Contact book icon -->
  <g class="icon" transform="translate(600,601)">
    <rect x="-21" y="-25" width="42" height="50" rx="3"/>
    <path d="M-14,-25 V25 M-21,-15 H-14 M-21,-5 H-14 M-21,5 H-14 M-21,15 H-14"/>
    <circle cx="5" cy="-10" r="5"/>
    <path d="M-6,7 Q-6,-3 5,-3 Q16,-3 16,7 Z"/>
    <path d="M-6,13 H16 M-6,18 H16"/>
  </g>
  <text class="module-label" x="600" y="658" text-anchor="middle">CONTACTS</text>

  <!-- Browser / globe icon -->
  <g class="icon" transform="translate(225,806)">
    <rect x="-24" y="-24" width="48" height="46" rx="2"/>
    <path d="M-24,-14 H24 M8,-19 H20"/>
    <circle class="icon-fill" cx="-18" cy="-19" r="1.6"/>
    <circle class="icon-fill" cx="-13" cy="-19" r="1.6"/>
    <circle class="icon-fill" cx="-8" cy="-19" r="1.6"/>
    <circle cx="0" cy="9" r="17"/>
    <ellipse cx="0" cy="9" rx="7" ry="17"/>
    <path d="M-17,9 H17 M-14,0 H14 M-14,18 H14"/>
  </g>
  <text class="module-label" x="275" y="809">WEBSITES &amp; LEADS</text>

  <!-- Phone icon -->
  <g class="icon" transform="translate(822,808)">
    <rect x="-16" y="-24" width="28" height="50" rx="4"/>
    <path d="M-7,-20 H3 M-10,-10 H6 M-10,-5 H6 M-10,0 H6 M-10,5 H6 M-10,10 H2"/>
    <path d="M-5,21 H1"/>
    <circle cx="18" cy="-18" r="11"/>
    <circle class="icon-fill" cx="14" cy="-18" r="2"/>
    <circle class="icon-fill" cx="21" cy="-23" r="2"/>
    <circle class="icon-fill" cx="21" cy="-13" r="2"/>
    <path d="M14,-18 L21,-23 M14,-18 L21,-13"/>
  </g>
  <text class="module-label" x="876" y="809">MOBILE</text>
</svg>

<aside class="legend">
  <div class="legend-swatch"></div>
  <p class="legend-text">Shaded areas indicate<br>Paywall feature</p>
</aside>
</body>
</html>
```